Business Card Design Project

Business Card design based on logo.
Updates

I need business card, letterhead, envelope, and if possible, Powerpoint slide template.

On front of business card: Just logo- and  my name and title:  Harriet Lindqvist, Principal

On reverse-logo and the rest of the contact info:

4871 Quarry Lane
Davis, CA 95618
650-318-2764
hl@brackenstudyworks.example

On letterhead-Just logo at top, at bottom  the rest-very small along the bottom

On PPT slide-just the logo.

I also want to try a few other colors-I like lime/dark grey (not black) but would like to try Sienna, maybe also indigo or bright blue-green.

I forgot to add-

On the business card-switch to vertical on reverse side and put:

Reverse side-switch to vertical and list:

Harriet Lindqvist
Principal
Bracken Study Works, LLC

650-318-2764

4871 Quarry Lane
Davis, CA 95618

Harriet Lindqvist
Principal

650-318-2764

4871 Quarry Lane
Davis, CA 95618

I have another project at the same time-for Stationery. Feel free to submit to that one also.

That one includes letterhead, envelope, PPT slide, folder cover sheet-HL

Industry/Entity Type

Business

Requirements
Must have
• Must use logo-preferably lime green version-with gray, not black or just 2-tone -logo on colored background.

```html
<!DOCTYPE html>
<html lang="en">
<head>
<meta charset="utf-8">
<title>Bracken Study Works — Business Cards</title>
<link href="https://fonts.googleapis.com/css2?family=Didact+Gothic&family=Libre+Baskerville&family=PT+Sans:wght@400;700&display=swap" rel="stylesheet">
<style>
  :root {
    --lime: #97b840;
    --charcoal: #2b2b2b;
    --slate: #4a4a4c;
    --ink: #1f1f1f;
    --paper: #ffffff;
    --backdrop: #8c4a22;
    --rule: #c9c9c9;
  }
  * { margin: 0; padding: 0; box-sizing: border-box; }
  html, body { width: 1200px; height: 716px; overflow: hidden; }
  body { background: var(--backdrop); position: relative; font-family: "PT Sans", sans-serif; }

  .card { position: absolute; width: 503px; height: 287px; background: var(--paper); overflow: hidden; }
  .card--contact { left: 85px; top: 55px; }
  .card--dark    { left: 622px; top: 60px; background: var(--charcoal); }
  .card--wordmark{ left: 86px; top: 375px; }
  .card--centered{ left: 622px; top: 380px; }

  .brand { font-family: "Libre Baskerville", serif; color: var(--slate); font-weight: 400; display: flex; align-items: center; gap: 10px; white-space: nowrap; }
  .brand__mark { width: 14px; height: 14px; background: var(--lime); flex: none; }

  /* contact card */
  .card--contact .brand { position: absolute; left: 22px; top: 122px; font-size: 17px; }
  .divider { position: absolute; left: 274px; top: 39px; width: 1px; height: 137px; background: var(--rule); }
  .holder { position: absolute; left: 285px; top: 40px; }
  .holder__name { color: var(--lime); font-weight: 700; font-size: 19px; line-height: 1.1; }
  .holder__title { color: var(--ink); font-size: 15px; margin-top: 3px; }
  .contacts { position: absolute; left: 285px; top: 102px; list-style: none; }
  .contacts li { display: flex; align-items: center; gap: 5px; font-size: 13px; color: var(--ink); height: 21px; white-space: nowrap; }
  .contacts svg { width: 10px; height: 10px; flex: none; }
  .wave { position: absolute; left: 0; bottom: 0; width: 503px; height: 287px; }
  .address { position: absolute; left: 0; right: 0; top: 263px; text-align: center; color: var(--paper); font-family: "Didact Gothic", sans-serif; font-size: 13px; letter-spacing: 1px; }

  /* shared url line */
  .url { position: absolute; left: 0; right: 0; text-align: center; font-family: "Didact Gothic", sans-serif; font-size: 18px; letter-spacing: 2px; color: var(--ink); white-space: nowrap; }
  .card--dark .url { top: 258px; color: var(--paper); }
  .card--wordmark .url { top: 255px; }
  .card--centered .url { top: 256px; }

  .card--dark .brand { position: absolute; left: 0; right: 0; top: 110px; justify-content: center; color: var(--paper); font-size: 26px; }
  .card--dark .brand__mark { background: var(--paper); }

  .card--wordmark .brand { position: absolute; left: 0; right: 0; top: 118px; justify-content: center; font-size: 34px; }

  .card--centered .brand { position: absolute; left: 0; right: 0; top: 150px; justify-content: center; font-size: 28px; }
</style>
</head>
<body>

  <section class="card card--contact">
    <svg class="wave" viewBox="0 0 503 287" aria-hidden="true">
      <path d="M0,218 C110,262 250,268 503,212 L503,287 L0,287 Z" fill="var(--lime)"/>
      <path d="M0,214 C100,255 240,262 503,206 L503,212 C250,268 110,262 0,222 Z" fill="var(--slate)"/>
    </svg>
    <div class="brand"><span class="brand__mark"></span>Bracken Study Works</div>
    <div class="divider"></div>
    <div class="holder">
      <p class="holder__name">Harriet Lindqvist</p>
      <p class="holder__title">Principal</p>
    </div>
    <ul class="contacts">
      <li><svg viewBox="0 0 10 10"><path d="M2,1 L4,1 L4.5,3 L3.3,3.8 C3.9,5.2 4.8,6.1 6.2,6.7 L7,5.5 L9,6 L9,8 C5,9 1,5 2,1 Z" fill="var(--lime)"/></svg>650-318-2764</li>
      <li><svg viewBox="0 0 10 10"><path d="M5,0.5 C2.8,0.5 1.5,2.1 1.5,3.9 C1.5,6.2 5,9.5 5,9.5 C5,9.5 8.5,6.2 8.5,3.9 C8.5,2.1 7.2,0.5 5,0.5 Z" fill="var(--lime)"/><circle cx="5" cy="3.9" r="1.3" fill="var(--paper)"/></svg>4871 Quarry Lane</li>
      <li><svg viewBox="0 0 10 10"><rect x="0.5" y="2" width="9" height="6.5" fill="var(--lime)"/><path d="M0.8,2.3 L5,5.8 L9.2,2.3" stroke="var(--paper)" stroke-width="0.9" fill="none"/></svg>hl@brackenstudyworks.example</li>
      <li><svg viewBox="0 0 10 10"><circle cx="5" cy="5" r="4.3" fill="none" stroke="var(--lime)" stroke-width="1.2"/><path d="M0.8,5 H9.2 M5,0.8 C2.5,3.5 2.5,6.5 5,9.2 C7.5,6.5 7.5,3.5 5,0.8" stroke="var(--lime)" stroke-width="0.8" fill="none"/></svg>www.brackenstudyworks.example</li>
    </ul>
    <p class="address">4871 Quarry Lane, Davis, CA 95618</p>
  </section>

  <section class="card card--dark">
    <div class="brand"><span class="brand__mark"></span>Bracken Study Works</div>
    <p class="url">www.brackenstudyworks.example</p>
  </section>

  <section class="card card--wordmark">
    <div class="brand"><span class="brand__mark"></span>Bracken Study Works</div>
    <p class="url">www.brackenstudyworks.example</p>
  </section>

  <section class="card card--centered">
    <div class="brand"><span class="brand__mark"></span>Bracken Study Works</div>
    <p class="url">www.brackenstudyworks.example</p>
  </section>

</body>
</html>
```